Stationery Design Project

I need a design that is simple, clean and modern, in square style, bold font.
The majority of the design needs to be White and Black with a splash of Red colour.
I would like a design for business cards and letter heads with the following information.
Name, Title, Phone, Fax, Email, Website and company ABN number

Target Market(s)

25 to 65 years old real estate clients

Industry/Entity Type

Business

Requirements
Must have
• All designs must incorporate Company Logo, Name, Title, Phone, Fax, Email, Website and company ABN number

```html
<!DOCTYPE html>
<html lang="en">
<head>
<meta charset="utf-8">
<title>Northgate Real Estate – Business Card</title>
<link rel="stylesheet" href="https://fonts.googleapis.com/css2?family=PT+Sans:wght@400;700&display=swap">
<style>
  :root {
    --stage: #ebe8e3;
    --white: #ffffff;
    --black: #231f20;
    --red: #d52a2a;
    --text-light: #ffffff;
    --font: "PT Sans", Arial, sans-serif;
  }
  * { box-sizing: border-box; margin: 0; padding: 0; }
  html, body {
    width: 1200px; height: 402px; overflow: hidden;
    background: var(--stage); font-family: var(--font);
  }
  .canvas { position: relative; width: 1200px; height: 402px; }

  .card { position: absolute; overflow: hidden; }

  /* Front */
  .card-front {
    left: 66px; top: 56px; width: 512px; height: 292px;
    background: var(--white);
  }
  .brand-frame {
    position: absolute; left: 145px; top: 26px; width: 222px; height: 125px;
    border: 4px solid var(--black); border-radius: 16px;
    display: flex; flex-direction: column; align-items: center; justify-content: center;
    color: var(--black); font-weight: 700; font-size: 22px; line-height: 1.15;
    letter-spacing: 1px; text-transform: uppercase; text-align: center;
  }
  .name-band {
    position: absolute; left: 0; top: 176px; width: 100%; height: 29px;
    background: var(--red); color: var(--text-light);
    display: flex; align-items: center; justify-content: center;
    font-size: 16px;
  }
  .name-band .person { font-weight: 700; margin-right: 5px; }
  .contact-bar {
    position: absolute; left: 0; top: 209px; width: 100%; height: 83px;
    background: var(--black); color: var(--text-light); font-size: 13.5px;
  }
  .contact-col { position: absolute; top: 24px; line-height: 18px; }
  .contact-col.phones { left: 38px; }
  .contact-col.online { left: 162px; }
  .contact-col.address { left: 323px; }
  .contact-row { display: flex; align-items: center; gap: 5px; white-space: nowrap; }
  .contact-row svg { width: 11px; height: 11px; fill: var(--text-light); flex: none; }
  .divider {
    position: absolute; top: 22px; width: 1.5px; height: 40px; background: var(--text-light);
  }
  .divider.one { left: 146px; }
  .divider.two { left: 308px; }

  /* Back */
  .card-back {
    left: 626px; top: 54px; width: 514px; height: 294px;
    background: var(--red);
  }
  .brand-frame-back {
    position: absolute; left: 107px; top: 44px; width: 304px; height: 167px;
    border: 5px solid var(--white); border-radius: 22px;
    display: flex; flex-direction: column; align-items: center; justify-content: center;
    color: var(--white); font-weight: 700; font-size: 30px; line-height: 1.15;
    letter-spacing: 1.5px; text-transform: uppercase; text-align: center;
  }
  .abn {
    position: absolute; left: 0; top: 229px; width: 100%; text-align: center;
    color: var(--text-light); font-size: 17px;
  }
</style>
</head>
<body>
<main class="canvas">

  <section class="card card-front" aria-label="Business card front">
    <div class="brand-frame">
      <span>Northgate</span>
      <span>Real Estate</span>
    </div>

    <div class="name-band">
      <span class="person">Your Name,</span><span class="title">Title</span>
    </div>

    <div class="contact-bar">
      <div class="contact-col phones">
        <div class="contact-row">
          <svg viewBox="0 0 24 24" aria-hidden="true"><path d="M6.6 10.8a15.1 15.1 0 0 0 6.6 6.6l2.2-2.2c.3-.3.7-.4 1-.2 1.1.4 2.3.6 3.6.6.6 0 1 .4 1 1V20c0 .6-.4 1-1 1A17 17 0 0 1 3 4c0-.6.4-1 1-1h3.5c.6 0 1 .4 1 1 0 1.3.2 2.5.6 3.6.1.3 0 .7-.2 1z"/></svg>
          <span>123-456-7890</span>
        </div>
        <div class="contact-row">
          <svg viewBox="0 0 24 24" aria-hidden="true"><path d="M7 2h10a2 2 0 0 1 2 2v16a2 2 0 0 1-2 2H7a2 2 0 0 1-2-2V4a2 2 0 0 1 2-2zm0 3v13h10V5zm5 14.2a1 1 0 1 0 0 .01z"/></svg>
          <span>123-456-7890</span>
        </div>
      </div>

      <span class="divider one"></span>

      <div class="contact-col online">
        <div class="contact-row">
          <svg viewBox="0 0 24 24" aria-hidden="true"><path d="M3 5h18a1 1 0 0 1 1 1v12a1 1 0 0 1-1 1H3a1 1 0 0 1-1-1V6a1 1 0 0 1 1-1zm1 2.5V17h16V7.5l-8 5.2z M4.5 7 12 11.8 19.5 7z"/></svg>
          <span>info@mailbox.com</span>
        </div>
        <div class="contact-row">
          <svg viewBox="0 0 24 24" aria-hidden="true"><circle cx="12" cy="12" r="10"/></svg>
          <span>www.website.com</span>
        </div>
      </div>

      <span class="divider two"></span>

      <div class="contact-col address">
        <div class="contact-row"><span>Street Name, City Name</span></div>
        <div class="contact-row"><span>State, City Zip Code 000</span></div>
      </div>
    </div>
  </section>

  <section class="card card-back" aria-label="Business card back">
    <div class="brand-frame-back">
      <span>Northgate</span>
      <span>Real Estate</span>
    </div>
    <p class="abn">ABN;123456789</p>
  </section>

</main>
</body>
</html>
```